Business Card Design - ChoiceCraft

Looking for creative, modern design, two sided for ChoiceCraft that is consistent with color and feel of website www.choicecraftpro.net.
Updates

Back of card will be used to promote products or have a quote revolving around decisions, change, leadership, innovation, creativity. Back should also have space to promote website, but optional to use the icon. Front of the card will need to use the icon and have standard place for name, job title, phone and email. We are not looking to put a mailing address or fax. Also want space to place a few words/phrase explaining what we do...such as individual growth and organizational development or tools, training, information...in addition, want the facebook icon small on the front somewhere as we are also on facebook.

Vector file uploaded of icon.

Target Market(s)

Professional coaching for individual growth and organizational development

Industry/Entity Type

Business

Requirements
Must have
• Icon...see attached.

```html
<!DOCTYPE html>
<html lang="en">
<head>
<meta charset="utf-8">
<title>ChoiceCraft Business Card</title>
<link rel="stylesheet" href="https://fonts.googleapis.com/css2?family=Arimo:wght@400;700&family=Tinos:wght@400;700&display=swap">
<style>
  :root {
    --backdrop: #b9bcbf;
    --card: #ffffff;
    --card-edge: #d4d6d8;
    --navy: #2b3272;
    --brand-blue: #1f86c8;
    --accent-blue: #2a93d5;
    --mark-fill: #8fb8dd;
    --mark-light: #cfe1f1;
    --text-grey: #4a4a4a;
    --text-dark: #222222;
  }
  * { box-sizing: border-box; margin: 0; padding: 0; }
  html, body {
    width: 1200px; height: 380px; overflow: hidden;
    background: var(--backdrop);
  }
  .canvas { position: relative; width: 1200px; height: 380px; }
  .card {
    position: absolute; top: 38px; width: 526px; height: 300px;
    background: var(--card); border: 1px solid var(--card-edge);
  }
  .card--front { left: 57px; font-family: "Tinos", "Times New Roman", serif; }
  .card--back { left: 611px; font-family: "Arimo", Arial, sans-serif; }

  /* Front */
  .holder {
    position: absolute; top: 20px; width: 100%; text-align: center;
    color: var(--navy); font-size: 19px; font-weight: 700;
  }
  .holder .title { font-size: 14px; font-weight: 400; }
  .brand-dot {
    position: absolute; left: 117px; top: 55px; width: 110px; height: 110px;
    border-radius: 50%;
    background: radial-gradient(circle at 40% 40%, var(--mark-light), var(--mark-fill));
  }
  .brand-name {
    position: absolute; left: 231px; top: 100px;
    color: var(--brand-blue); font-size: 27px; font-weight: 700;
  }
  .tagline {
    position: absolute; top: 199px; width: 100%; text-align: center;
    color: var(--text-grey); font-size: 14px; line-height: 15px;
  }
  .phone {
    position: absolute; top: 250px; width: 100%; text-align: center;
    color: var(--text-grey); font-size: 14px;
  }
  .contacts {
    position: absolute; top: 266px; width: 100%;
    display: flex; justify-content: center; align-items: center; gap: 9px;
    color: var(--text-grey); font-size: 14px;
  }
  .contacts span { display: inline-flex; align-items: center; gap: 4px; }
  .contacts svg { width: 10px; height: 10px; }
  .social-square { width: 9px; height: 9px; background: var(--text-grey); display: inline-block; }

  /* Back */
  .quotes { position: absolute; left: 28px; top: 24px; list-style: none; }
  .quote { position: relative; height: 53px; padding-left: 45px; }
  .quote-dot {
    position: absolute; left: 0; top: 3px; width: 22px; height: 22px; border-radius: 50%;
    background: radial-gradient(circle at 40% 40%, var(--mark-light), var(--mark-fill));
  }
  .quote-text { color: var(--text-dark); font-size: 14px; }
  .quote-text .mark { font-family: "Tinos", serif; font-weight: 700; font-size: 22px; line-height: 0; }
  .quote-text .mark--open { position: absolute; left: 29px; top: 10px; }
  .quote-author { color: var(--accent-blue); font-size: 14px; font-weight: 700; margin-top: 2px; padding-left: 9px; }
  .back-dot {
    position: absolute; left: 386px; top: 170px; width: 100px; height: 112px; border-radius: 50%;
    background: radial-gradient(circle at 40% 40%, var(--mark-light), var(--mark-fill));
  }
</style>
</head>
<body>
<main class="canvas">
  <section class="card card--front" aria-label="Card front">
    <p class="holder">Your Name, <span class="title">Title</span></p>
    <div class="brand-dot" aria-hidden="true"></div>
    <p class="brand-name">ChoiceCraft</p>
    <p class="tagline">Supporting individual growth<br>and organizational development, or tools, training, information</p>
    <p class="phone">&#9990; 123-456-789</p>
    <p class="contacts">
      <span><svg viewBox="0 0 10 10" aria-hidden="true"><rect x="0.5" y="2" width="9" height="6" fill="none" stroke="currentColor"/><path d="M0.5 2 L5 5.5 L9.5 2" fill="none" stroke="currentColor"/></svg>info@choicecraftpro.net</span>
      <span><svg viewBox="0 0 10 10" aria-hidden="true"><circle cx="5" cy="5" r="4.5" fill="none" stroke="currentColor"/><ellipse cx="5" cy="5" rx="2" ry="4.5" fill="none" stroke="currentColor"/><line x1="0.5" y1="5" x2="9.5" y2="5" stroke="currentColor"/></svg>www.choicecraftpro.net</span>
      <span><i class="social-square" aria-hidden="true"></i>/choicecraftpro</span>
    </p>
  </section>

  <section class="card card--back" aria-label="Card back">
    <ul class="quotes">
      <li class="quote"><i class="quote-dot"></i><p class="quote-text"><span class="mark mark--open">&ldquo;</span>Try not to become a man of success, but rather a man of value.<span class="mark">&rdquo;</span></p><p class="quote-author">- Alden Ward</p></li>
      <li class="quote"><i class="quote-dot"></i><p class="quote-text"><span class="mark mark--open">&ldquo;</span>The only constant is change.<span class="mark">&rdquo;</span></p><p class="quote-author">- Theron Vale</p></li>
      <li class="quote"><i class="quote-dot"></i><p class="quote-text"><span class="mark mark--open">&ldquo;</span>We are what we repeatedly do. Excellence is not an act, it is a habit.<span class="mark">&rdquo;</span></p><p class="quote-author">- Corin Matthis</p></li>
      <li class="quote"><i class="quote-dot"></i><p class="quote-text"><span class="mark mark--open">&ldquo;</span>Simplicity is the ultimate sophistication.<span class="mark">&rdquo;</span></p><p class="quote-author">- Lorenzo Bellari</p></li>
      <li class="quote"><i class="quote-dot"></i><p class="quote-text"><span class="mark mark--open">&ldquo;</span>Life is not fair - get used to it.<span class="mark">&rdquo;</span></p><p class="quote-author">- Will Garner</p></li>
    </ul>
    <div class="back-dot" aria-hidden="true"></div>
  </section>
</main>
</body>
</html>
```